Business Card for Coastal Tundrabridge Advisory

We need a business card for Coastal Tundrabridge Advisory. The company website address is provided below. The company logo is attached. We provide specialized permafrost services to the mining, transportation, and oil & gas industries. The card should be prepared for:
Matthias Korhonen, PhD.
Coastal Tundrabridge Advisory
PO Box 418259
Quillwater, Alaska 99642
Direct: +1-907-555-0143
Email: mkorhonen@tundrabridgeadvisory.example
Website: www.coastaltundrabridgeadvisory.example

```html
<!DOCTYPE html>
<html lang="en">
<head>
<meta charset="utf-8">
<title>Coastal Tundrabridge Advisory – Business Card</title>
<link href="https://fonts.googleapis.com/css2?family=Montserrat:wght@400;500;600;700&display=swap" rel="stylesheet">
<style>
  :root {
    --backdrop: #9b9b9b;
    --card-light: #ffffff;
    --card-dark: #121822;
    --ink: #141a24;
    --ink-soft: #1f2530;
    --mark-dark: #2b3648;
  }
  * { margin: 0; padding: 0; box-sizing: border-box; }
  html, body {
    width: 1093px; height: 1200px; overflow: hidden;
    background: var(--backdrop);
    font-family: "Montserrat", sans-serif;
    color: var(--ink);
  }
  .canvas { position: relative; width: 1093px; height: 1200px; }
  .card {
    position: absolute; left: 265px; width: 580px; height: 363px;
    border-radius: 18px; overflow: hidden;
  }
  .card--front { top: 225px; background: var(--card-light); }
  .card--back { top: 616px; background: var(--card-dark); }

  .brand-name {
    position: absolute; left: 40px; top: 191px; width: 190px;
    font-weight: 600; font-size: 15px; line-height: 18px;
    letter-spacing: 0.04em; text-transform: uppercase; text-align: center;
    color: var(--ink);
  }
  .divider {
    position: absolute; left: 241px; top: 121px; width: 1.5px; height: 167px;
    background: var(--ink);
  }
  .details { position: absolute; left: 250px; top: 119px; }
  .person-name { font-weight: 700; font-size: 20px; line-height: 24px; }
  .person-title { font-weight: 500; font-size: 13px; line-height: 16px; margin-top: 1px; color: var(--ink-soft); }
  .address { margin-top: 11px; margin-left: 2px; font-size: 13.5px; line-height: 16.5px; }
  .contacts { list-style: none; margin-top: 17px; margin-left: 2px; }
  .contacts li { display: flex; align-items: center; height: 25.5px; font-size: 12.5px; }
  .contacts svg { width: 13px; height: 13px; margin-right: 10px; flex: none; fill: var(--ink); }

  .back-brand {
    position: absolute; left: 0; right: 0; top: 148px;
    text-align: center; font-weight: 600; font-size: 28px; line-height: 34px;
    letter-spacing: 0.08em; text-transform: uppercase; color: var(--mark-dark);
  }
</style>
</head>
<body>
<div class="canvas">
  <section class="card card--front">
    <div class="brand-name">Coastal Tundrabridge<br>Advisory</div>
    <div class="divider"></div>
    <div class="details">
      <h1 class="person-name">Matthias Korhonen, PhD.</h1>
      <p class="person-title">Managing Director</p>
      <p class="address">PO Box 418259<br>Quillwater, Alaska 99642</p>
      <ul class="contacts">
        <li>
          <svg viewBox="0 0 24 24" aria-hidden="true"><path d="M6.6 10.8a15.1 15.1 0 0 0 6.6 6.6l2.2-2.2c.3-.3.7-.4 1-.2 1.1.4 2.3.6 3.6.6.6 0 1 .4 1 1V20c0 .6-.4 1-1 1A17 17 0 0 1 3 4c0-.6.4-1 1-1h3.5c.6 0 1 .4 1 1 0 1.3.2 2.5.6 3.6.1.3 0 .7-.2 1z"/></svg>
          +1-907-555-0143
        </li>
        <li>
          <svg viewBox="0 0 24 24" aria-hidden="true"><path d="M2 5h20v14H2z M2 6l10 7 10-7" fill="none" stroke="#141a24" stroke-width="0"/><path d="M2 5h20v2l-10 6L2 7z"/><path d="M2 9l10 6 10-6v10H2z"/></svg>
          mkorhonen@tundrabridgeadvisory.example
        </li>
        <li>
          <svg viewBox="0 0 24 24" aria-hidden="true"><circle cx="12" cy="12" r="10"/><path d="M7 6c2 1 3 3 2 5s1 3 0 5l-2-1-1-4zM14 4c2 0 5 2 5 5-1 1-3 0-4 2s1 4-1 6-2-2-2-4-2-2-1-4 3-1 3-3z" fill="#ffffff"/></svg>
          www.coastaltundrabridgeadvisory.example
        </li>
      </ul>
    </div>
  </section>

  <section class="card card--back">
    <div class="back-brand">Coastal Tundrabridge<br>Advisory</div>
  </section>
</div>
</body>
</html>
```